Online Guide to Events for Adults in Pennsylvania

9GrownupsOnTour is an online event advertisement business for local companies throughout the state to feature their events, music festivals, restaurant, bed & breakfast promotions, wineries and vineyards, theatre and entertainment. The business is geared towards adults. The homepage shall be sleek and elegant, yet user friendly and events searchable on from the homepage. The homepage shall also have an area for local event advertisement spots that rotate every few seconds. Color scheme should include a deep or wine red and some black.

I have attached the current logo and a couple of photos for use. Feel free to use any photos you have available as an example.

A few examples of websites that are similar to what I am looking for:

http://hollowcreekvino.example/

http://www.roamtrevarrow.example/index.asp

I also enjoy the design of many of the websites built by townwright.example.

Target Market(s)

Adults, ages 18 - 65

Industry/Entity Type

Advertising

Number of Pages Required

2 page

Font styles to use
Decorative
Script

Requirements
Must have
• Searchable field on homepage whether it is in the form of a state map with counties, or search by zip code, county, event type and month.
Should not have
• Nothing that appears cartoon like.

```html
<!DOCTYPE html>
<html lang="en">
<head>
<meta charset="utf-8">
<title>9GrownupsOnTour — Online Event Advertisement</title>
<link rel="stylesheet" href="https://fonts.googleapis.com/css2?family=Raleway:wght@300;400;700;800&family=Open+Sans:wght@400;600&display=swap">
<style>
:root{
  --red:#d9232a;
  --red-deep:#b5121b;
  --red-bright:#ee2a2a;
  --ink:#1c1c1c;
  --muted:#6f6f6f;
  --panel:#f4f4f4;
  --footer:#2b2b2b;
  --white:#ffffff;
}
*{box-sizing:border-box;margin:0;padding:0}
html,body{width:858px;height:1200px;overflow:hidden;background:var(--white)}
body{position:relative;font-family:"Open Sans",Arial,sans-serif;color:var(--ink)}
.abs{position:absolute}

/* header */
.brand{left:70px;top:44px;display:flex;align-items:center;gap:7px}
.brand-mark{width:10px;height:10px;background:var(--ink)}
.brand-name{font-family:"Raleway",sans-serif;font-weight:700;font-size:13px;letter-spacing:1.2px;color:var(--ink);text-transform:uppercase}
.nav{top:47px;left:0;width:858px;font-family:"Raleway",sans-serif;font-size:12px;color:#333}
.nav span{position:absolute;white-space:nowrap}
.nav .active{color:var(--red)}

/* hero */
.hero{left:0;top:84px;width:858px;height:340px;
  background:radial-gradient(ellipse at 30% 80%,#a8141a 0%,transparent 55%),
             radial-gradient(ellipse at 80% 30%,#f04a4a 0%,transparent 60%),
             linear-gradient(180deg,#e8383b 0%,#d8242a 55%,#c01a20 100%)}
.scallop{left:0;width:858px;height:8px;
  background:radial-gradient(circle at 5px 0,var(--white) 4.5px,transparent 5px) 0 0/10px 8px repeat-x}
.scallop.top{top:84px}
.scallop.bottom{top:416px;transform:scaleY(-1)}
.hero-kicker{left:70px;top:128px;font-family:"Raleway",sans-serif;font-weight:300;font-size:22px;color:var(--white)}
.hero-title{left:70px;top:159px;font-family:"Raleway",sans-serif;font-weight:800;font-size:35px;color:var(--white)}
.hero-sub{left:72px;top:210px;width:270px;font-size:8.6px;line-height:14.5px;color:var(--white)}
.btn-book{left:70px;top:262px;width:105px;height:42px;border:2px solid var(--white);border-radius:2px;
  font-family:"Raleway",sans-serif;font-weight:800;font-size:14px;color:var(--white);
  display:flex;align-items:center;justify-content:center;letter-spacing:.3px}
.video-frame{left:435px;top:125px;width:353px;height:194px;background:rgba(255,255,255,.35)}
.video-still{left:444px;top:134px;width:335px;height:176px;
  background:radial-gradient(ellipse at 55% 75%,#b98a4a 0%,#5a3a1a 30%,transparent 60%),
             linear-gradient(180deg,#2a2116 0%,#1a140d 100%)}
.play{left:579px;top:194px;width:67px;height:44px;border-radius:9px;background:var(--red-bright);
  display:flex;align-items:center;justify-content:center}

/* search */
.field{top:337px;height:42px;width:133px;background:var(--white);
  font-size:10.5px;color:#777;display:flex;align-items:center;justify-content:space-between;padding:0 10px 0 11px}
.btn-find{left:629px;top:337px;width:159px;height:42px;background:var(--ink);color:var(--white);
  font-family:"Raleway",sans-serif;font-weight:800;font-size:15px;display:flex;align-items:center;justify-content:center;gap:8px;letter-spacing:.3px}

/* welcome */
.section-title{font-family:"Raleway",sans-serif;font-weight:400;font-size:23px;color:var(--ink);white-space:nowrap}
.section-title em{font-style:normal;color:var(--red)}
.welcome-title{left:0;top:464px;width:858px;text-align:center}
.welcome-text{left:72px;top:504px;width:714px;text-align:center;font-size:8.6px;line-height:15px;color:var(--muted)}
.btn-read{left:384px;top:552px;width:91px;height:37px;background:var(--red);border-radius:2px;color:var(--white);
  font-size:10px;display:flex;align-items:center;justify-content:center;box-shadow:0 2px 3px rgba(0,0,0,.15)}

/* services */
.services{left:0;top:619px;width:858px;height:282px;background:var(--panel)}
.services-title{left:70px;top:646px}
.arrow{top:650px;width:30px;height:28px;background:#444;display:flex;align-items:center;justify-content:center}
.card{top:694px;width:230px;height:169px}
.card-photo{width:230px;height:115px}
.card-bar{width:230px;height:54px;background:linear-gradient(180deg,var(--red-bright) 0%,var(--red-deep) 100%);
  font-family:"Raleway",sans-serif;font-size:23px;color:var(--white);padding:12px 0 0 14px}
.card-shadow{left:20px;top:166px;width:190px;height:20px;border-radius:50%;
  background:radial-gradient(ellipse at center,rgba(0,0,0,.18) 0%,transparent 70%)}

/* events */
.events-title{left:0;top:926px;width:858px;text-align:center}
.event-photo{top:995px;width:125px;height:99px}
.event-head{top:995px;font-family:"Raleway",sans-serif;font-size:15px;color:var(--red);white-space:nowrap}
.event-date{top:1017px;font-size:8.6px;color:#888}
.event-text{top:1036px;width:200px;font-size:8.6px;line-height:14.5px;color:#555}
.event-link{top:1081px;font-size:8.6px;color:var(--red)}

/* footer */
.footer{left:0;top:1139px;width:858px;height:61px;background:var(--footer)}
.footer-links{left:70px;top:1156px;font-size:8.6px;color:#aaa;white-space:nowrap}
.footer-copy{left:70px;top:1172px;font-size:8.6px;color:#aaa}
.social{top:1156px;width:23px;height:22px;background:#3a3a3a}
</style>
</head>
<body>

<header>
  <div class="abs brand"><span class="brand-mark"></span><span class="brand-name">9GrownupsOnTour</span></div>
  <nav class="abs nav">
    <span class="active" style="left:489px">Features</span>
    <span style="left:562px">Pricing</span>
    <span style="left:621px">Services</span>
    <span style="left:692px">Sign up</span>
    <span style="left:758px">Log in</span>
  </nav>
</header>

<section>
  <div class="abs hero" role="img" aria-label="Concert crowd with raised hands, tinted red"></div>
  <div class="abs scallop top"></div>
  <div class="abs scallop bottom"></div>

  <div class="abs hero-kicker">Online Event</div>
  <h1 class="abs hero-title">Advertisement</h1>
  <p class="abs hero-sub">events, music festivals, restaurant, bed &amp; breakfast promotions, wineries and vineyards, theatre and entertainment.</p>
  <div class="abs btn-book">BOOK NOW</div>

  <div class="abs video-frame"></div>
  <div class="abs video-still" role="img" aria-label="Wine glass, bottle, cheese, bread and candle on a dark table"></div>
  <div class="abs play"><svg width="12" height="14" viewBox="0 0 12 14"><path d="M1 1 L11 7 L1 13 Z" fill="#fff"/></svg></div>

  <div class="abs field" style="left:70px">ZIP CODE</div>
  <div class="abs field" style="left:210px">COUNTY<svg width="8" height="6" viewBox="0 0 8 6"><path d="M1 1 L4 4 L7 1" stroke="#444" stroke-width="1.4" fill="none"/></svg></div>
  <div class="abs field" style="left:350px">EVENT TYPE<svg width="8" height="6" viewBox="0 0 8 6"><path d="M1 1 L4 4 L7 1" stroke="#444" stroke-width="1.4" fill="none"/></svg></div>
  <div class="abs field" style="left:490px">MONTH<svg width="10" height="10" viewBox="0 0 10 10"><rect x="0.5" y="1.5" width="9" height="8" fill="none" stroke="#444"/><rect x="0.5" y="1.5" width="9" height="2.5" fill="#444"/><path d="M2.5 5.5h1M5 5.5h1M7.5 5.5h1M2.5 7.5h1M5 7.5h1" stroke="#444"/></svg></div>
  <div class="abs btn-find">FIND NOW <svg width="14" height="14" viewBox="0 0 14 14"><circle cx="6" cy="6" r="4.3" stroke="#fff" stroke-width="2" fill="none"/><path d="M9.2 9.2 L13 13" stroke="#fff" stroke-width="2.4"/></svg></div>
</section>

<section>
  <h2 class="abs section-title welcome-title">WELCOME TO <em>9GROWNUPSONTOUR</em></h2>
  <p class="abs welcome-text">Nemo enim ipsam voluptatem quia voluptas sit aspernatur aut odit aut fugit, sed quia consequuntur magni dolores eos qui ratione voluptatem sequi nesciunt. Neque porro quis-quam est, qui dolorem ipsum quia dolor sit amet, consectetur, adipisci velit</p>
  <div class="abs btn-read">Read More</div>
</section>

<section>
  <div class="abs services"></div>
  <h2 class="abs section-title services-title">OUR <em>SERVICES</em></h2>
  <div class="abs arrow" style="left:727px"><svg width="8" height="12" viewBox="0 0 8 12"><path d="M6 1 L1 6 L6 11" stroke="#fff" stroke-width="1.4" fill="none"/></svg></div>
  <div class="abs arrow" style="left:758px"><svg width="8" height="12" viewBox="0 0 8 12"><path d="M2 1 L7 6 L2 11" stroke="#fff" stroke-width="1.4" fill="none"/></svg></div>

  <div class="abs card" style="left:70px">
    <div class="abs card-shadow"></div>
    <div class="abs card-photo" role="img" aria-label="Microphone on stage under purple lights" style="background:linear-gradient(120deg,#3a1f3a 0%,#a8687a 40%,#6b2b8a 70%,#2a1030 100%)"></div>
    <div class="abs card-bar" style="top:115px">Music Festivals</div>
  </div>
  <div class="abs card" style="left:315px">
    <div class="abs card-shadow"></div>
    <div class="abs card-photo" role="img" aria-label="Plated tomato and pepper salad" style="background:radial-gradient(ellipse at 50% 60%,#d8563a 0%,#c8a050 35%,#e8e8e8 75%)"></div>
    <div class="abs card-bar" style="top:115px">Restaurant</div>
  </div>
  <div class="abs card" style="left:558px">
    <div class="abs card-shadow"></div>
    <div class="abs card-photo" role="img" aria-label="Wine bottle and glass at sunset over vineyards" style="background:linear-gradient(180deg,#7a6a3a 0%,#c8b070 45%,#8a6a30 80%,#3a2a10 100%)"></div>
    <div class="abs card-bar" style="top:115px">wineries</div>
  </div>
</section>

<section>
  <h2 class="abs section-title events-title">RECENT <em>EVENTS</em></h2>

  <div class="abs event-photo" role="img" aria-label="Trumpet under colourful stage lights" style="left:70px;background:linear-gradient(135deg,#3a2a6a 0%,#c03a8a 40%,#2a1a4a 70%,#0a0a1a 100%)"></div>
  <div class="abs event-head" style="left:212px">LOREM IPSUM DOLOR</div>
  <div class="abs event-date" style="left:214px">Jun 14,2015</div>
  <p class="abs event-text" style="left:212px">Nemo enim ipsam voluptatem quia voluptas sit aspernatur aut odit aut fugit,...</p>
  <div class="abs event-link" style="left:212px">View Details</div>

  <div class="abs event-photo" role="img" aria-label="Couple dancing under stage lights" style="left:457px;background:radial-gradient(ellipse at 60% 30%,#8a3ad0 0%,#2a1a8a 40%,#05051a 85%)"></div>
  <div class="abs event-head" style="left:599px">LOREM IPSUM DOLOR</div>
  <div class="abs event-date" style="left:601px">Jun 14,2015</div>
  <p class="abs event-text" style="left:599px">Nemo enim ipsam voluptatem quia voluptas sit aspernatur aut odit aut fugit,...</p>
  <div class="abs event-link" style="left:599px">View Details</div>
</section>

<footer>
  <div class="abs footer"></div>
  <div class="abs footer-links">Home &nbsp;/&nbsp; Features &nbsp;/&nbsp; Pricing / &nbsp;Services &nbsp;/&nbsp; Sign up &nbsp; / &nbsp;Log in</div>
  <div class="abs footer-copy">Copyright © 2015</div>
  <div class="abs social" style="left:657px"></div>
  <div class="abs social" style="left:684px"></div>
  <div class="abs social" style="left:711px"></div>
  <div class="abs social" style="left:738px"></div>
  <div class="abs social" style="left:765px"></div>
</footer>

</body>
</html>
```